Reach the Summit - PPT Template with Splash Slide

We are looking for a PPT template that has 4 slides.
1. Splash slide (Creative, fun, no content, a visual representation of the theme)
2. Section header slide
3. Content Slide
4. Content Slide, another design option
The theme is 'Reach the Summit'. The design should reflect this theme.
The colors should be in Purple (#864B99), Blue (#0A80C2), and Green (#52B054).

```html
<!DOCTYPE html>
<html lang="en">
<head>
<meta charset="utf-8">
<title>Reach the Summit – Slide Template</title>
<link href="https://fonts.googleapis.com/css2?family=Open+Sans:wght@400;600;700&display=swap" rel="stylesheet">
<style>
  :root {
    --purple: #864B99;
    --purple-title: #6E3C82;
    --purple-deep: #5E346E;
    --blue: #0A80C2;
    --blue-mid: #2E93D1;
    --sky-light: #CFE6F4;
    --green: #52B054;
    --yellow: #FFC13B;
    --red: #E2293A;
    --orange: #FF7A00;
    --white: #FFFFFF;
    --page: #FFFFFF;
  }
  * { box-sizing: border-box; margin: 0; padding: 0; }
  html, body { width: 1050px; height: 1200px; overflow: hidden; background: var(--page); }
  body { position: relative; font-family: "Open Sans", Arial, sans-serif; color: var(--white); }

  .slide { position: absolute; width: 458px; height: 343px; overflow: hidden; }
  .slide--r1 { top: 30px; } .slide--r2 { top: 428px; } .slide--r3 { top: 827px; }
  .slide--left { left: 30px; } .slide--right { left: 562px; }

  .scene {
    position: absolute; inset: 0;
    background: linear-gradient(120deg, var(--blue) 0%, var(--blue-mid) 40%, #8CC4E6 72%, var(--sky-light) 88%, var(--purple-deep) 94%, var(--purple-deep) 100%);
  }
  .scene--splash {
    background:
      linear-gradient(120deg, rgba(10,128,194,0) 30%, rgba(250,220,120,0.75) 72%, rgba(94,52,110,1) 92%),
      linear-gradient(160deg, var(--blue) 0%, #6FB3DE 60%, var(--sky-light) 100%);
  }

  .slide-title { position: absolute; left: 23px; top: 46px; font-size: 18px; font-weight: 600; color: var(--purple-title); line-height: 1.1; white-space: nowrap; }
  .slide-subtitle { position: absolute; left: 23px; top: 71px; font-size: 10.5px; color: var(--white); }

  .hero-title { position: absolute; left: 23px; top: 163px; font-size: 28px; font-weight: 600; color: var(--white); line-height: 1.1; white-space: nowrap; }
  .hero-meta { position: absolute; left: 23px; top: 203px; font-size: 14px; color: var(--purple); line-height: 1.5; }

  .content { position: absolute; left: 23px; top: 113px; width: 412px; font-size: 8.4px; line-height: 1.15; }
  .content--section { left: 63px; top: 145px; width: 312px; }
  .section-title { left: 63px; top: 110px; }
  .lead { font-weight: 700; font-size: 9.6px; margin-bottom: 3px; white-space: nowrap; }
  .content p { margin-bottom: 4px; }
  .bullets { list-style: none; }
  .bullets li { position: relative; padding-left: 8px; margin-top: 4px; }
  .bullets li::before { content: "•"; position: absolute; left: 0; }
  .bullets .lvl2 { padding-left: 20px; }
  .bullets .lvl2::before { content: "o"; left: 12px; font-size: 7px; top: 1px; }
  .bullets .lvl3 { padding-left: 31px; }
  .bullets .lvl3::before { content: "–"; left: 22px; }

  .footer { position: absolute; left: 34px; top: 327px; font-size: 6px; display: flex; gap: 6px; }
  .footer strong { font-weight: 700; }
  .footer--chart { left: 20px; }

  .chart-title { position: absolute; left: 135px; top: 99px; font-size: 10px; font-weight: 700; }
  .pie { position: absolute; left: 0; top: 0; }
  .legend { position: absolute; left: 239px; top: 158px; width: 42px; height: 97px; background: rgba(207,230,244,0.55); padding: 5px 0 0 10px; list-style: none; font-size: 5.5px; color: var(--white); }
  .legend li { height: 16.3px; display: flex; align-items: flex-start; gap: 2px; }
  .swatch { width: 4px; height: 4px; margin-top: 1.5px; }
</style>
</head>
<body>

<!-- Splash -->
<section class="slide slide--r1 slide--left">
  <div class="scene scene--splash" role="img" aria-label="Sky illustration with sun rays and clouds, a climber scaling a purple cliff on the right"></div>
  <h1 class="hero-title">Presentation Title</h1>
  <div class="hero-meta"><p>Presentation subtitle</p><p>Date</p></div>
</section>

<!-- Section divider -->
<section class="slide slide--r1 slide--right">
  <div class="scene" role="img" aria-label="Blue sky with clouds and a climber on a purple cliff"></div>
  <h2 class="slide-title section-title">Section Divider</h2>
  <div class="content content--section">
    <p class="lead">Lorem ipsum dolor amet consectetur adipiscing elit.</p>
    <p>Pellentesque eget dapibus nulla. Suspendisse sed urna dui. Vestibulum suscipit, nisl vel tincidunt ornare, lacus diam ultricies ipsum, nec finibus diam enim et nibh.</p>
    <p>Phasellus porttitor quam nec diam interdum sagittis. Ut quis condimentum magna. Orci varius natoque penatibus et magnis dis parturient montes, nascetur ridiculus mus. Proin vel felis molestie, convallis erat id, viverra mi.</p>
    <p>Morbi faucibus dictum massa, elementum accumsan nunc condimentum porta. Sed consectetur nisi ac sagittis faucibus. Nullam ullamcorper ante ut urna imperdiet dictum. Maecenas a ex lobortis, condimentum augue in, aliquam enim.</p>
  </div>
  <div class="footer"><span>4</span><strong>Reach the Summit</strong></div>
</section>

<!-- Title and content -->
<section class="slide slide--r2 slide--left">
  <div class="scene" role="img" aria-label="Blue sky with clouds and a climber on a purple cliff"></div>
  <h2 class="slide-title">Title and Content</h2>
  <div class="content">
    <p class="lead">Lorem ipsum dolor sit amet consectetur adipiscing elit.</p>
    <p>Pellentesque eget dapibus nulla. Suspendisse sed urna dui. Vestibulum suscipit, nisl vel tincidunt ornare, lacus diam ultricies ipsum, nec finibus diam enim et nibh. Phasellus porttitor quam nec diam interdum sagittis. Phasellus sed nibh in leo posuere convallis in eget sem. Proin et enim eget sapien rutrum accumsan ac non ipsum. Mauris ex purus, egestas ut mauris eget, laoreet volutpat est.</p>
    <p>Praesent venenatis lectus non lacinia congue. Ut quis condimentum magna. Orci varius natoque penatibus et magnis dis parturient montes, nascetur ridiculus mus. Proin vel felis molestie, convallis erat id, viverra mi. Morbi faucibus dictum massa, elementum accumsan nunc condimentum porta. Sed consectetur nisi ac sagittis faucibus. Nullam ullamcorper ante ut urna imperdiet dictum. Maecenas a ex lobortis, condimentum augue in, aliquam enim.</p>
    <ul class="bullets">
      <li>Proin fermentum nunc sapien, eget commodo libero euismod non.</li>
      <li>Vivamus interdum volutpat malesuada.</li>
      <li>Curabitur sed lorem condimentum, tristique elit ac, bibendum turpis.</li>
      <li class="lvl2">Pellentesque dignissim nunc id efficitur efficitur.</li>
      <li class="lvl3">Praesent sed arcu ut magna porta pulvinar.</li>
      <li class="lvl3">In odio est, semper et rhoncus id, scelerisque et arcu.</li>
    </ul>
  </div>
  <div class="footer"><span>2</span><strong>Reach the Summit</strong></div>
</section>

<!-- Title and subtitle -->
<section class="slide slide--r2 slide--right">
  <div class="scene" role="img" aria-label="Blue sky with clouds and a climber on a purple cliff"></div>
  <h2 class="slide-title">Title and Subtitle</h2>
  <p class="slide-subtitle">Subtitle</p>
  <div class="content">
    <p class="lead">Lorem ipsum dolor sit amet consectetur adipiscing elit.</p>
    <p>Pellentesque eget dapibus nulla. Suspendisse sed urna dui. Vestibulum suscipit, nisl vel tincidunt ornare, lacus diam ultricies ipsum, nec finibus diam enim et nibh. Phasellus porttitor quam nec diam interdum sagittis. Phasellus sed nibh in leo posuere convallis in eget sem. Proin et enim eget sapien rutrum accumsan ac non ipsum. Mauris ex purus, egestas ut mauris eget, laoreet volutpat est.</p>
    <p>Praesent venenatis lectus non lacinia congue. Ut quis condimentum magna. Orci varius natoque penatibus et magnis dis parturient montes, nascetur ridiculus mus. Proin vel felis molestie, convallis erat id, viverra mi. Morbi faucibus dictum massa, elementum accumsan nunc condimentum porta. Sed consectetur nisi ac sagittis faucibus. Nullam ullamcorper ante ut urna imperdiet dictum. Maecenas a ex lobortis, condimentum augue in, aliquam enim.</p>
    <ul class="bullets">
      <li>Proin fermentum nunc sapien, eget commodo libero euismod non.</li>
      <li>Vivamus interdum volutpat malesuada.</li>
      <li>Curabitur sed lorem condimentum, tristique elit ac, bibendum turpis.</li>
      <li class="lvl2">Pellentesque dignissim nunc id efficitur efficitur.</li>
      <li class="lvl3">Praesent sed arcu ut magna porta pulvinar.</li>
      <li class="lvl3">In odio est, semper et rhoncus id, scelerisque et arcu.</li>
    </ul>
  </div>
  <div class="footer"><span>5</span><strong>Reach the Summit</strong></div>
</section>

<!-- Title only with chart -->
<section class="slide slide--r3 slide--left">
  <div class="scene" role="img" aria-label="Blue sky with clouds and a climber on a purple cliff"></div>
  <h2 class="slide-title">Title Only Slide</h2>
  <p class="chart-title">Lorem Ipsum</p>
  <svg class="pie" width="458" height="343" viewBox="0 0 458 343" aria-label="Pie chart of six levels">
    <path d="M141 206 L141 123 A83 83 0 0 1 160.7 125.3 Z" fill="var(--purple)"/>
    <path d="M141 206 L160.7 125.3 A83 83 0 0 1 188.6 138 Z" fill="var(--blue)"/>
    <path d="M141 206 L188.6 138 A83 83 0 0 1 215.6 169.6 Z" fill="var(--green)"/>
    <path d="M141 206 L215.6 169.6 A83 83 0 0 1 220.2 231 Z" fill="var(--yellow)"/>
    <path d="M141 206 L220.2 231 A83 83 0 0 1 165.3 285.4 Z" fill="var(--red)"/>
    <path d="M141 206 L165.3 285.4 A83 83 0 1 1 141 123 Z" fill="var(--orange)"/>
  </svg>
  <ul class="legend">
    <li><span class="swatch" style="background:var(--purple)"></span>Level 1</li>
    <li><span class="swatch" style="background:var(--blue)"></span>Level 2</li>
    <li><span class="swatch" style="background:var(--green)"></span>Level 3</li>
    <li><span class="swatch" style="background:var(--yellow)"></span>Level 4</li>
    <li><span class="swatch" style="background:var(--red)"></span>Level 5</li>
    <li><span class="swatch" style="background:var(--orange)"></span>Level 6</li>
  </ul>
  <div class="footer footer--chart"><span>3</span><strong>Reach the Summit</strong></div>
</section>

<!-- Title and subtitle only -->
<section class="slide slide--r3 slide--right">
  <div class="scene" role="img" aria-label="Blue sky with clouds and a climber on a purple cliff"></div>
  <h2 class="slide-title">Title and Subtitle Only</h2>
  <p class="slide-subtitle">Subtitle</p>
  <div class="footer"><span>6</span><strong>Reach the Summit</strong></div>
</section>

</body>
</html>
```